Re-Design an adult education portal

I need support to re-design an adult education portal. Currently the customer has an incomplete website which should be prepared in a new format.
I have the idea how to realize, but I have no clue how to design it. The hard thing is to have a "beautiful" website with available logo and main color. I hope you can support me.

Name of Website: moluvo (moluvo.ch)
Content: adult eduction for adult in safety at work, mountain climbing, dog school. various courses in different areas. But on old webpage is hard to find the different possibilities.
main color: Ral 6011 (green) -> #6C7C59
logo: you see on top of website the logo (2 dogs and a mountain with a colour gradient).

new website: for new webpage I decided to have a navigation for each section of education. In the main area I would like to have some pictures to give an idea what content is behind. At the moment it looks terrible, so I decided to use you as support for me to make the webpage prettier :). And maybe you have an better idea how to make it great. -> current state of new web page: https://moluvo.perch-net.ch/

Target Market(s)

adult eduction for adult in safety at work, mountain climbing, dog school

Number of Pages Required

1 page

Font styles to use
Serif
Sans Serif

Requirements
Must have
• As main color is set "Ral 6011" (green) -> #6C7C59

```html
<!DOCTYPE html>
<html lang="en">
<head>
<meta charset="utf-8">
<title>moluvo – Your Training and Course Partners</title>
<link rel="stylesheet" href="https://fonts.googleapis.com/css2?family=Lato:wght@400;700&family=Merriweather:wght@700;900&display=swap">
<style>
:root{
  --green:#6c7c59;
  --green-dark:#5b6a4a;
  --text:#4a4a4a;
  --muted:#666;
  --band:#f1f1ef;
  --footer:#58573f;
  --white:#fff;
}
*{box-sizing:border-box;margin:0;padding:0}
html,body{width:1200px;height:3646px;overflow:hidden}
body{position:relative;background:var(--white);font-family:"Lato",sans-serif;color:var(--text)}
.abs{position:absolute}
.photo{position:absolute}

/* header / hero */
.hero{left:0;top:0;width:1200px;height:524px;background:linear-gradient(180deg,#b9c1c9 0%,#dfe1e2 30%,#e9e6e1 50%,#9aa1a8 75%,#6f747b 100%)}
.logo{left:153px;top:11px;display:flex;align-items:center;gap:6px;background:var(--white);padding:8px 10px;height:43px;font-size:16px;color:var(--green);font-weight:700}
.logo .mark{width:14px;height:14px;background:var(--green)}
.nav{left:0;top:22px;width:1048px;height:20px}
.nav a{position:absolute;font-size:14px;color:#444;text-decoration:none;white-space:nowrap}
.nav a.active::after{content:"";position:absolute;left:0;right:0;top:32px;height:2px;background:var(--green)}
.hero-title{left:153px;top:156px;font-family:"Merriweather",serif;font-weight:900;font-size:38px;line-height:45px;color:#555}
.hero-sub{left:153px;top:258px;width:290px;font-size:14px;line-height:22px;color:var(--white)}
.btn{left:153px;top:320px;width:163px;height:51px;background:var(--green);color:var(--white);font-size:13px;font-weight:700;letter-spacing:.5px;display:flex;align-items:center;justify-content:center}

/* section headings */
.heading{position:absolute;left:0;width:1200px;text-align:center}
.heading span{display:inline-block;font-size:26px;font-weight:700;color:var(--green);padding-bottom:6px;border-bottom:2px solid var(--green);position:relative}
.heading span::after{content:"";position:absolute;left:50%;bottom:-7px;margin-left:-5px;border:5px solid transparent;border-top-color:var(--green);border-bottom:0}
.dots{position:absolute;background:#f4f4f1}

.about-text{left:535px;top:655px;width:512px;font-size:12.5px;line-height:22.6px;color:#444}
.about-text p+p{margin-top:22px}

.feature{position:absolute;height:154px}
.feature::before{content:"";position:absolute;left:0;top:0;width:52px;height:48px;border-left:2px solid var(--green);border-top:2px solid var(--green)}
.feature::after{content:"";position:absolute;right:0;bottom:0;width:52px;height:52px;border-right:2px solid var(--green);border-bottom:2px solid var(--green)}
.feature svg{position:absolute;top:22px}
.feature p{position:absolute;left:0;top:103px;font-size:10.5px;line-height:18px;color:#555}

/* courses */
.band{left:0;top:1206px;width:1200px;height:733px;background:var(--band)}
.card{position:absolute;width:274px;height:197px;box-shadow:0 2px 6px rgba(0,0,0,.18)}
.card .label{position:absolute;left:0;right:0;bottom:6px;text-align:center;color:var(--white);font-size:18px;font-weight:700;text-shadow:0 1px 3px rgba(0,0,0,.5)}
.card.hover .more{position:absolute;left:0;right:0;top:86px;text-align:center;color:var(--white);font-size:17px;font-weight:700}

/* trainers */
.subtitle{left:0;top:2035px;width:1200px;text-align:center;font-size:14px;color:#333}
.goal{left:153px;top:2143px;font-size:14px;color:var(--green);font-weight:700}
.goal::before{content:"";display:inline-block;border:5px solid transparent;border-left:7px solid #555;border-right:0;margin-right:8px;vertical-align:1px}
.trainer-text{left:150px;top:2183px;width:392px;font-size:13.5px;line-height:22.6px;color:#444}
.trainer-text p{padding-left:17px;position:relative}
.trainer-text p+p{margin-top:22px}
.tick{position:absolute;left:0;top:6px}
.overlay-title{left:627px;top:2257px;font-size:18px;color:var(--white);letter-spacing:.5px}
.overlay-sub{left:627px;top:2283px;font-size:6.5px;color:var(--white)}
.name{position:absolute;font-size:21px;color:#333;letter-spacing:.3px}
.qual{position:absolute;list-style:none;font-size:13.5px;color:#444}
.qual li{height:30px;line-height:30px;padding-left:21px;position:relative;white-space:nowrap}
.qual li svg{position:absolute;left:0;top:10px}

/* footer */
.footer{left:0;top:3369px;width:1200px;height:277px;background:var(--footer);color:var(--white)}
.fcol{position:absolute;top:44px}
.fcol h4{font-size:16px;font-weight:700;margin-bottom:15px}
.fcol li{list-style:none;font-size:13px;line-height:30px;display:flex;align-items:flex-start;gap:8px}
.fcol .ico{width:20px;height:20px;border-radius:50%;background:#7c7c63;margin-top:5px;flex:none}
.copy{position:absolute;left:0;width:1200px;top:245px;text-align:center;font-size:12.5px}
</style>
</head>
<body>

<!-- hero -->
<div class="photo hero" role="img" aria-label="Hiker in a red jacket facing a snowy alpine peak at sunrise"></div>
<div class="abs logo"><span class="mark"></span>moluvo</div>
<nav class="abs nav">
  <a style="left:525px">Occupational Safety</a>
  <a class="active" style="left:681px">First Aid</a>
  <a style="left:764px">Dog school</a>
  <a style="left:863px">CZV</a>
  <a style="left:922px">Mountain education</a>
</nav>
<h1 class="abs hero-title">Your Training and<br>Course Partners</h1>
<p class="abs hero-sub">We offer training that is tailored to your needs and skills.</p>
<div class="abs btn">GET STARTED</div>

<!-- about -->
<h2 class="heading" style="top:567px"><span>About Us</span></h2>
<div class="dots" style="left:106px;top:613px;width:127px;height:120px" role="img" aria-label="Dotted decoration"></div>
<div class="photo" style="left:153px;top:657px;width:310px;height:206px;background:linear-gradient(160deg,#8fae5a,#5e8a34 60%,#7a9b4b)" role="img" aria-label="Two trainers sitting in a meadow with their dogs"></div>
<div class="abs about-text">
  <p>In my professional career, I have experienced situation that have allowed me to mature the idea of giving every interested person a basic knowledge that allows him to react correctly and with the necessary calm in the event of an emergency, combining knowledge and skills of the different disciplines gives people security and trust in their actions.</p>
  <p>From our own experience it has been shown that the more professional you are prepared for borderline solutions, the safer and more successful an emergency situation can be mastered and even lives saved.</p>
</div>

<div class="feature" style="left:205px;top:910px;width:190px">
  <svg style="left:49px" width="70" height="70" viewBox="0 0 70 70" fill="none" stroke="#333" stroke-width="3">
    <path d="M35 6l5 0 2 8 6 3 7-4 7 7-4 7 3 6 8 2v10l-8 2-3 6 4 7-7 7-7-4-6 3-2 8H30l-2-8-6-3-7 4-7-7 4-7-3-6-8-2V30l8-2 3-6-4-7 7-7 7 4 6-3 2-8z" transform="translate(0 0) scale(.95) translate(2 0)"/>
    <circle cx="35" cy="35" r="12"/>
  </svg>
  <p>Train with tools from everyday life<br>and the familiar environment</p>
</div>
<div class="feature" style="left:518px;top:910px;width:163px">
  <svg style="left:36px" width="72" height="70" viewBox="0 0 72 70" fill="none" stroke="#333" stroke-width="2.5">
    <rect x="26" y="4" width="42" height="30"/>
    <path d="M32 26l9-8 7 5 12-11"/>
    <circle cx="14" cy="16" r="6"/><path d="M4 38v-8a10 10 0 0 1 20 0h12"/>
    <rect x="2" y="38" width="68" height="6"/>
    <circle cx="10" cy="52" r="4"/><circle cx="27" cy="52" r="4"/><circle cx="44" cy="52" r="4"/><circle cx="61" cy="52" r="4"/>
    <path d="M4 68v-6a6 6 0 0 1 12 0v6M21 68v-6a6 6 0 0 1 12 0v6M38 68v-6a6 6 0 0 1 12 0v6M55 68v-6a6 6 0 0 1 12 0v6"/>
  </svg>
  <p>Reality-based education and<br>training</p>
</div>
<div class="feature" style="left:805px;top:910px;width:212px">
  <svg style="left:54px" width="72" height="70" viewBox="0 0 72 70" fill="none" stroke="#333" stroke-width="3">
    <path d="M16 56V40a20 20 0 0 1 40 0v16"/>
    <rect x="8" y="56" width="56" height="10"/>
    <path d="M36 30a10 10 0 0 0-10 10"/>
    <path d="M36 4v10M12 12l6 6M60 12l-6 6M2 34h8M62 34h8"/>
  </svg>
  <p>Train in such a way that automatisms<br>can be retrieved by acting consistently<br>in an emergency</p>
</div>

<h2 class="heading" style="top:1110px"><span>Best Training and Courses for You</span></h2>

<!-- courses -->
<div class="abs band"></div>
<div class="card" style="left:153px;top:1244px;background:linear-gradient(180deg,#3c3a33,#6b6450 60%,#2e2c27)" role="img" aria-label="Forklift inside a warehouse container"><span class="label">Forklift Courses</span></div>
<div class="card" style="left:463px;top:1244px;background:linear-gradient(160deg,#6a4732,#4b3222 60%,#7a5640)" role="img" aria-label="Protective gear laid out on a wooden table"><span class="label">PPE</span></div>
<div class="card" style="left:773px;top:1244px;background:linear-gradient(180deg,#7ea0c8,#b9c4c8 45%,#8b8a70 75%,#6d6a5a)" role="img" aria-label="Aerial work platform lifting a worker near a vineyard"><span class="label">Aerial Work Platform</span></div>
<div class="card" style="left:153px;top:1474px;background:linear-gradient(180deg,#8a8d90,#b0a89a 50%,#8a7a68)" role="img" aria-label="Dog on a leash sitting beside its owner"><span class="label">Dog School</span></div>
<div class="card" style="left:463px;top:1474px;background:linear-gradient(180deg,#b8c4d0,#7b7b7e 55%,#3a3a3c)" role="img" aria-label="First aiders with rescue backpacks in a town square"><span class="label">First Aiders</span></div>
<div class="card hover" style="left:773px;top:1474px;background:linear-gradient(160deg,#8dbb4a,#6ea13a)" role="img" aria-label="Resuscitation training on a manikin"><span class="more">Learn More</span><span class="label">Sanitary Training</span></div>
<div class="card" style="left:153px;top:1705px;background:linear-gradient(135deg,#8a3a30,#c9453a 45%,#e8e2da 70%,#6a6a6a)" role="img" aria-label="Fire engine behind a warning road sign"><span class="label">BLS AGD</span></div>
<div class="card" style="left:463px;top:1705px;background:linear-gradient(180deg,#5f86c4,#c7d0d8 50%,#8a8c8e)" role="img" aria-label="Fire truck parked in front of a fire station"><span class="label">CZV</span></div>
<div class="card" style="left:773px;top:1705px;background:linear-gradient(135deg,#5c5448,#9e9588 50%,#e9e7e3)" role="img" aria-label="Climbers on a steep rock face"><span class="label">Mountain Training</span></div>

<!-- trainers -->
<h2 class="heading" style="top:1982px"><span>Your Trainers and Instructors</span></h2>
<p class="abs subtitle">Lukas and Anna Brenner with heart and soul for you</p>
<div class="dots" style="left:967px;top:2104px;width:127px;height:118px" role="img" aria-label="Dotted decoration"></div>
<p class="abs goal">Goal: Professional, Safe and Calm action in all situations!</p>
<div class="abs trainer-text">
  <p><svg class="tick" width="12" height="10" viewBox="0 0 12 10"><path d="M1 5l3.5 3.5L11 1" fill="none" stroke="#6c7c59" stroke-width="2"/></svg>Our instructors are excellently trained: theoretically sound, tried and tested in practice, methodical and didactic trained. Their continuous training guarantees highly qualified and motivated employees with the ultimate goal of preparing the participants individually for future assignments / emergencies. As a collegial team, we achieve our goals with each other through respectful, fair and honest dealings.</p>
  <p>We are convinced that learning should be fun, motivate and that our students can benefit from adapted, versatile and practical training in all life situations.</p>
</div>
<div class="photo" style="left:582px;top:2148px;width:465px;height:279px;background:linear-gradient(170deg,#4d6fa8,#7d8a6e 40%,#6b5a44 70%,#9a9488)" role="img" aria-label="Both trainers sitting on rocks with their dogs"></div>
<p class="abs overlay-title">Your trainer</p>
<p class="abs overlay-sub">Lukas &amp; Anna Brenner with heart and soul for you</p>

<div class="photo" style="left:167px;top:2493px;width:412px;height:327px;background:linear-gradient(180deg,#b8c0c8,#d9dde0 40%,#5b6a78 75%,#2f4a5e)" role="img" aria-label="Portrait of trainer Lukas Brenner in front of snowy mountains"></div>
<div class="dots" style="left:122px;top:2745px;width:126px;height:120px" role="img" aria-label="Dotted decoration"></div>
<h3 class="name" style="left:638px;top:2484px">LUKAS BRENNER</h3>
<ul class="qual" style="left:617px;top:2526px">
  <li><svg width="12" height="10" viewBox="0 0 12 10"><path d="M1 5l3.5 3.5L11 1" fill="none" stroke="#6c7c59" stroke-width="2"/></svg>Dipl. Mountain Guide &amp; dipl. Snow sports instructors</li>
  <li><svg width="12" height="10" viewBox="0 0 12 10"><path d="M1 5l3.5 3.5L11 1" fill="none" stroke="#6c7c59" stroke-width="2"/></svg>Dipl. Expert in the Piste &amp; Rescue Service &amp;</li>
  <li><svg width="12" height="10" viewBox="0 0 12 10"><path d="M1 5l3.5 3.5L11 1" fill="none" stroke="#6c7c59" stroke-width="2"/></svg>Instructor cable cars Switzerland</li>
  <li><svg width="12" height="10" viewBox="0 0 12 10"><path d="M1 5l3.5 3.5L11 1" fill="none" stroke="#6c7c59" stroke-width="2"/></svg>Avalanche Dog Guide &amp; Trainer RVO</li>
  <li><svg width="12" height="10" viewBox="0 0 12 10"><path d="M1 5l3.5 3.5L11 1" fill="none" stroke="#6c7c59" stroke-width="2"/></svg>Emergency Assistant Instructor (Alpine Safety Certification)</li>
  <li><svg width="12" height="10" viewBox="0 0 12 10"><path d="M1 5l3.5 3.5L11 1" fill="none" stroke="#6c7c59" stroke-width="2"/></svg>BLS AED Instructor NRA</li>
  <li><svg width="12" height="10" viewBox="0 0 12 10"><path d="M1 5l3.5 3.5L11 1" fill="none" stroke="#6c7c59" stroke-width="2"/></svg>Examination expert ATF (Everyday Suitable Family Dog)</li>
  <li><svg width="12" height="10" viewBox="0 0 12 10"><path d="M1 5l3.5 3.5L11 1" fill="none" stroke="#6c7c59" stroke-width="2"/></svg>Examination expert NHB (National Dog Owner Brevet)</li>
  <li><svg width="12" height="10" viewBox="0 0 12 10"><path d="M1 5l3.5 3.5L11 1" fill="none" stroke="#6c7c59" stroke-width="2"/></svg>BVET Dog Trainer</li>
  <li><svg width="12" height="10" viewBox="0 0 12 10"><path d="M1 5l3.5 3.5L11 1" fill="none" stroke="#6c7c59" stroke-width="2"/></svg>RVO Avalanche Dog Guide (Regional Valley Rescue Organisation)</li>
  <li><svg width="12" height="10" viewBox="0 0 12 10"><path d="M1 5l3.5 3.5L11 1" fill="none" stroke="#6c7c59" stroke-width="2"/></svg>Welding dog guide</li>
  <li><svg width="12" height="10" viewBox="0 0 12 10"><path d="M1 5l3.5 3.5L11 1" fill="none" stroke="#6c7c59" stroke-width="2"/></svg>hunter</li>
</ul>

<h3 class="name" style="left:173px;top:2940px">ANNA BRENNER</h3>
<ul class="qual" style="left:153px;top:2982px">
  <li><svg width="12" height="10" viewBox="0 0 12 10"><path d="M1 5l3.5 3.5L11 1" fill="none" stroke="#6c7c59" stroke-width="2"/></svg>Specialist Health</li>
  <li><svg width="12" height="10" viewBox="0 0 12 10"><path d="M1 5l3.5 3.5L11 1" fill="none" stroke="#6c7c59" stroke-width="2"/></svg>BLS - AED - Instructor NRA</li>
  <li><svg width="12" height="10" viewBox="0 0 12 10"><path d="M1 5l3.5 3.5L11 1" fill="none" stroke="#6c7c59" stroke-width="2"/></svg>Emergency Assistant Instructor (Alpine Safety Certification)</li>
  <li><svg width="12" height="10" viewBox="0 0 12 10"><path d="M1 5l3.5 3.5L11 1" fill="none" stroke="#6c7c59" stroke-width="2"/></svg>Examination expert ATF (Everyday Suitable Family Dog)</li>
  <li><svg width="12" height="10" viewBox="0 0 12 10"><path d="M1 5l3.5 3.5L11 1" fill="none" stroke="#6c7c59" stroke-width="2"/></svg>Examination expert NHB (National Dog Owner Brevet)</li>
  <li><svg width="12" height="10" viewBox="0 0 12 10"><path d="M1 5l3.5 3.5L11 1" fill="none" stroke="#6c7c59" stroke-width="2"/></svg>BEVET Dog Trainer</li>
  <li><svg width="12" height="10" viewBox="0 0 12 10"><path d="M1 5l3.5 3.5L11 1" fill="none" stroke="#6c7c59" stroke-width="2"/></svg>huntress</li>
</ul>
<div class="photo" style="left:635px;top:2939px;width:414px;height:331px;background:linear-gradient(180deg,#8f8a88,#3b3a3c 35%,#d4602a 55%,#e6e4e2 85%)" role="img" aria-label="Trainer Anna Brenner in an orange jacket cheering in the snow"></div>
<div class="dots" style="left:969px;top:3194px;width:125px;height:120px" role="img" aria-label="Dotted decoration"></div>

<!-- footer -->
<footer class="abs footer">
  <div class="fcol" style="left:153px">
    <h4>Our Courses</h4>
    <ul><li>Occupational Safety</li><li>First Aid</li><li>Dog school</li><li>CZV</li><li>Mountain education</li></ul>
  </div>
  <div class="fcol" style="left:422px">
    <h4>Contact Us</h4>
    <ul>
      <li><svg style="margin-top:9px;flex:none" width="13" height="13" viewBox="0 0 13 13"><rect x="1" y="1" width="11" height="11" rx="1" fill="#fff"/><circle cx="6.5" cy="5" r="2" fill="#58573f"/><path d="M3 10a3.5 3 0 0 1 7 0z" fill="#58573f"/></svg><span style="line-height:20px;margin-top:4px">moluvo gmbh<br>Talweg 27<br>3930 Visp</span></li>
      <li><svg style="margin-top:9px;flex:none" width="13" height="13" viewBox="0 0 24 24"><path fill="#fff" d="M6.6 10.8a15 15 0 0 0 6.6 6.6l2.2-2.2a1 1 0 0 1 1-.25 11.4 11.4 0 0 0 3.6.6 1 1 0 0 1 1 1V20a1 1 0 0 1-1 1A17 17 0 0 1 3 4a1 1 0 0 1 1-1h3.5a1 1 0 0 1 1 1c0 1.25.2 2.45.6 3.6a1 1 0 0 1-.25 1z"/></svg>+41 79 000 12 34</li>
      <li><svg style="margin-top:10px;flex:none" width="13" height="10" viewBox="0 0 13 10"><rect width="13" height="10" fill="#fff"/><path d="M0 0l6.5 5L13 0" fill="none" stroke="#58573f" stroke-width="1.3"/></svg>info@moluvo.ch</li>
    </ul>
  </div>
  <div class="fcol" style="left:696px">
    <h4>Social Media</h4>
    <ul><li><span class="ico"></span>Community</li><li><span class="ico"></span>Photo Stream</li><li><span class="ico"></span>News Feed</li></ul>
  </div>
  <div class="fcol" style="left:938px">
    <h4>Forms</h4>
    <ul><li>Policies</li><li>Model</li><li>Certificate Quali-Ed</li><li>Imprint</li></ul>
  </div>
  <p class="copy">©2021 moluvo | All Rights Reserved</p>
</footer>

</body>
</html>
```